Unique Realty Niche needs a web design

Starting Note: Please do not use the colors from the logo on quickhousebarnowl.net which is their current website. This logo will eventually change but it is what they have now.

This website is a realty website that caters to individuals who want to rent out their homes (investors) and those who want to rent a home (Tenants). We provide no credit check to rent a home from a investor at a higher cost for the tenant to balance risk. Good renters with bad credit are able to rent or buy a house from investors who are registered in our system.

Target Market(s)

Home Owners trying to rent out their homes, and people looking to rent.

Industry/Entity Type

House

Requirements
Must have
• Main Navigation links: Home - Our Story - tenant - owner - contact us

A log in form somewhere on the page.

Key themes in the site are as follows: The site needs to be clean and professional looking i.e. no grunge. I provided some color palettes below, these are not set in stone and if you know of a good palette(s) our client is very open to all suggestions. The main navigation needs to stay on top but other on page navigations could go on left (preferably) On the left or the right will be featured listings for some homes. It will be between 3 to 5 listings showing at one time. (Please see quickhousebarnowl.net for example)

Example Color Palettes:
http://hueplank.example.org/#themeID/1634353
http://hueplank.example.org/#themeID/166988
http://hueplank.example.org/#themeID/1638382
http://hueplank.example.org/#themeID/1677863

Example Websites That Client Likes:
NOTE: Very Flexible, no need to duplicate these below.
http://www.fernlotgroupvx.net/
http://www.tqbgrove.net/
http://www.wubalestewards.net/index.php?pr=Home_Page

Nice to have
• It would be nice to have short easy to read paragraphs accompanied by a photo so scanning is easy on the site. Then in later pages we will have more text when there is more detail needed. We know you wont come up with the content but concept would be nice.

```html
<!DOCTYPE html>
<html lang="en">
<head>
<meta charset="utf-8">
<title>Barn Owl Property Stewards</title>
<link href="https://fonts.googleapis.com/css2?family=Arimo:wght@400;700&family=PT+Sans&family=Tinos&display=swap" rel="stylesheet">
<style>
:root{
  --ink:#111;
  --charcoal:#2b2b2b;
  --black:#000;
  --white:#fff;
  --accent:#e8481c;
  --red:#d40000;
  --panel:rgba(120,120,120,.82);
  --soft-grey:#cfcfcf;
  --field-grey:#555;
  --line:#ddd;
}
*{box-sizing:border-box;margin:0;padding:0}
html,body{width:975px;height:1200px;overflow:hidden;background:var(--white)}
body{position:relative;font-family:Arimo,Arial,sans-serif;color:var(--ink)}
.abs{position:absolute}

.top-bar{left:0;top:0;width:975px;height:29px;background:var(--charcoal)}
.top-bar svg{position:absolute;left:556px;top:29px}
.login{position:absolute;right:20px;top:5px;display:flex;align-items:center;gap:6px;font-size:11px;color:#ccc}
.login .login-field{width:96px;height:18px;background:#444;border:1px solid #666;color:#aaa;font-size:10px;line-height:16px;padding-left:5px}
.login .login-btn{height:18px;padding:0 9px;background:#111;border:1px solid #666;color:var(--white);font-size:10px;line-height:16px}

.brand{left:36px;top:42px;display:flex;align-items:center;gap:18px}
.brand-mark{width:84px;height:84px;border-radius:50%;background:var(--line)}
.brand-name{font-family:"PT Sans",sans-serif;font-size:23px;line-height:25px;color:var(--accent)}

.main-nav{left:550px;top:69px;display:flex}
.main-nav a{font-size:12.5px;color:var(--ink);text-decoration:none;margin-right:24px}

.hero{left:21px;top:151px;width:924px;height:321px}
.hero-photo{position:absolute;inset:0;background:linear-gradient(180deg,#8a8f96 0%,#5c4a3e 35%,#6f6a63 60%,#3d6b2c 100%)}
.hero-shadow{left:60px;top:474px;width:800px;height:10px;background:radial-gradient(ellipse at center,rgba(0,0,0,.18),transparent 70%)}
.hero-caption{position:absolute;left:0;bottom:0;width:100%;height:50px;background:rgba(0,0,0,.45);color:var(--white);font-size:12px;line-height:15px;padding:10px 20px}
.hero-caption p{width:580px}
.hero-arrow{position:absolute;top:138px;width:26px;height:44px;background:var(--black)}
.hero-arrow.prev{left:0;border-radius:0 22px 22px 0}
.hero-arrow.next{right:0;border-radius:22px 0 0 22px}
.hero-arrow svg{position:absolute;top:16px}

.search{left:664px;top:179px;width:240px;height:270px;background:var(--panel);padding:18px 16px}
.search h2{font-family:Tinos,serif;font-weight:400;font-size:18px;color:var(--red);margin:0 0 12px 4px}
.search label{display:block;font-size:12px;color:var(--ink);margin:0 0 8px 4px}
.field{background:var(--white);height:20px;border:1px solid #999}
.select{height:20px;background:var(--white);border:1px solid #666;position:relative}
.select::after{content:"";position:absolute;right:2px;top:2px;width:14px;height:14px;background:#ddd;border:1px solid #888}
.select::before{content:"";position:absolute;right:6px;top:8px;border:4px solid transparent;border-top-color:#000;z-index:1}
.row{display:flex;align-items:center;gap:4px}
.search-btn{display:block;margin:26px auto 0;width:108px;height:31px;background:#111;color:var(--white);font-size:12.5px;border:1px solid #444;text-align:center;line-height:29px}

h3.section{position:absolute;font-family:Tinos,serif;font-weight:400;font-size:17px;color:var(--ink);letter-spacing:.3px}
.welcome-text{left:22px;top:532px;width:662px;font-size:12.2px;line-height:25px;text-align:justify}
.more{position:absolute;font-family:Tinos,serif;font-size:13px;color:var(--red);text-decoration:none}

.video{left:705px;top:532px;width:253px;height:185px;background:var(--black);color:var(--white);overflow:hidden}
.video-title{position:absolute;left:12px;top:10px;font-size:17px;white-space:nowrap}
.video-by{position:absolute;left:12px;top:32px;font-size:10px;color:#ccc}
.replay{position:absolute;left:88px;top:70px;display:flex;align-items:center;gap:6px;font-size:16px}
.replay i{display:block;width:26px;height:20px;border-radius:4px;background:#ddd}
.controls{position:absolute;left:0;bottom:0;width:100%;height:24px;background:#222;display:flex;align-items:center;font-size:10px;gap:8px;padding:0 8px}
.progress{flex:1;height:4px;background:var(--red);border-radius:2px;position:relative}
.progress::after{content:"";position:absolute;right:-4px;top:-4px;width:12px;height:12px;border-radius:50%;background:#eee}

.testimonial{position:absolute;top:790px;width:330px;height:120px}
.avatar{position:absolute;left:0;top:0;width:84px;height:112px;background:linear-gradient(180deg,#cfcfcf 0%,#9a9a9a 50%,#2d2d2d 100%);border-radius:40px 40px 6px 6px}
.testimonial p{position:absolute;left:96px;top:4px;width:220px;font-family:Tinos,serif;font-size:12px;line-height:25px;text-align:justify}
.divider{left:355px;top:795px;width:1px;height:100px;background:linear-gradient(180deg,transparent,#bbb,transparent)}

.newsletter{left:703px;top:753px;width:255px;height:154px;background:var(--soft-grey);border-radius:8px;padding:12px}
.newsletter h4{font-family:Tinos,serif;font-weight:400;font-size:17px;margin-bottom:14px}
.email{height:37px;background:var(--field-grey);color:var(--white);font-size:12.5px;line-height:37px;padding-left:16px;border-radius:6px}
.submit{position:absolute;right:14px;top:99px;width:89px;height:32px;background:#111;color:var(--white);font-size:12.5px;text-align:center;line-height:30px;border:1px solid #444}

.carousel-arrow{position:absolute;top:1011px;width:24px;height:24px;background:linear-gradient(#fafafa,#ccc);border:1px solid #bbb;border-radius:3px}
.carousel-arrow svg{position:absolute;left:6px;top:5px}
.listing{position:absolute;top:976px;width:159px;height:101px;background:var(--white);border:1px solid var(--line);box-shadow:0 2px 3px rgba(0,0,0,.15);padding:4px}
.listing div{width:100%;height:91px}

.footer{left:0;top:1121px;width:975px;height:79px;background:var(--black);color:var(--white)}
.footer-nav{position:absolute;left:20px;top:22px;display:flex;gap:28px;font-size:12.5px}
.copyright{position:absolute;left:20px;top:47px;font-size:12px}
.connect{position:absolute;right:12px;top:14px;display:flex;align-items:center;gap:8px;font-size:12.5px}
.connect span.dot{width:29px;height:29px;border-radius:50%;background:#dfe6ee}
</style>
</head>
<body>
<header>
  <div class="abs top-bar">
    <svg width="16" height="11"><path d="M0 0h16L8 11z" fill="#2b2b2b"/></svg>
    <form class="login">
      <span>Member login</span>
      <span class="login-field">Username</span>
      <span class="login-field">Password</span>
      <span class="login-btn">LOGIN</span>
    </form>
  </div>
  <div class="abs brand">
    <span class="brand-mark"></span>
    <span class="brand-name">Barn Owl<br>Property Stewards</span>
  </div>
  <nav class="abs main-nav">
    <a href="#">Home</a><a href="#">Our Story</a><a href="#">Tenant</a><a href="#">Owner</a><a href="#">Contact us</a>
  </nav>
</header>

<section class="abs hero">
  <div class="hero-photo" role="img" aria-label="Photo of a shingled suburban house with white windows and green shrubs"></div>
  <div class="hero-caption"><p>Lorem Ipsum is simply dummy text of the printing and typesetting industry. Lorem Ipsum has been the industry's standard dummy text ever since the 1500s,</p></div>
  <span class="hero-arrow prev"><svg width="10" height="12" style="left:7px"><path d="M7 1L2 6l5 5" stroke="#fff" stroke-width="2" fill="none"/></svg></span>
  <span class="hero-arrow next"><svg width="10" height="12" style="left:9px"><path d="M3 1l5 5-5 5" stroke="#fff" stroke-width="2" fill="none"/></svg></span>
</section>
<div class="abs hero-shadow"></div>

<form class="abs search">
  <h2>Find Your Property</h2>
  <label>Price per month</label>
  <div class="row" style="margin-bottom:10px"><div class="field" style="width:90px"></div><span style="font-size:12px">To</span><div class="field" style="width:98px"></div></div>
  <label>Location</label>
  <div class="select" style="width:100px;margin-bottom:12px"></div>
  <div class="row" style="gap:0"><label style="width:106px">Availability</label><label>Property Type</label></div>
  <div class="row" style="gap:8px"><div class="select" style="width:100px"></div><div class="select" style="width:100px"></div></div>
  <span class="search-btn">SEARCH</span>
</form>

<h3 class="section" style="left:22px;top:504px">WELCOME</h3>
<p class="abs welcome-text">Quick House Barn Owl was founded in April, 2005 with every intention on being the best. You will quickly find we offer a variety of services to the real estate investment market. We have built an empire over a short time, which includes a large network of investors, builders, realtors, mortgage companies, and credit repair agencies. We are here to help you in every aspect of buying, selling, or leasing a home. We specialize in buying homes no matter what the situation with no money out of your pocket!! That's right, No Closing Costs, No Commissions, No Fees!! Facing Divorce or Foreclosure? No Equity? Relocating? House Vacant? Let us be the ones to relieve you of your stress or put some cash back in your pocket. Take just a few minutes and fill out our online form to sell your home quickly. One of our many private investors will contact you with-in 48 hours to discuss your specific needs and concerns after submitting the "Sell A Home" form.</p>
<a class="more" href="#" style="left:600px;top:742px">View More&gt;&gt;</a>

<div class="abs video">
  <div class="video-title">Fernlot Rental Services</div>
  <div class="video-by">by fernlotrentals</div>
  <div class="replay"><i></i>Replay</div>
  <div class="controls"><span>&#9654;</span><span>3:45 / 3:45</span><span class="progress"></span><span>&#9633;</span></div>
</div>

<h3 class="section" style="left:24px;top:759px">TESTIMONIALS</h3>
<div class="testimonial" style="left:20px">
  <div class="avatar" role="img" aria-label="Illustrated avatar of a man in a suit"></div>
  <p>Lorem Ipsum is simply dummy text of the printing and typesetting industry. Lorem Ipsum has been the industry's standard dummy text ever since the 1500s,</p>
  <a class="more" href="#" style="left:235px;top:104px">View More&gt;&gt;</a>
</div>
<div class="abs divider"></div>
<div class="testimonial" style="left:373px">
  <div class="avatar" role="img" aria-label="Illustrated avatar of a man in a suit"></div>
  <p style="left:97px">Lorem Ipsum is simply dummy text of the printing and typesetting industry. Lorem Ipsum has been the industry's standard dummy text ever since the 1500s,</p>
  <a class="more" href="#" style="left:243px;top:107px">View More&gt;&gt;</a>
</div>

<form class="abs newsletter">
  <h4>NEWS LETTER</h4>
  <div class="email">Enter Email - ID</div>
  <span class="submit">SUBMIT</span>
</form>

<h3 class="section" style="left:25px;top:935px">FEATURED HOMES FOR SALE</h3>
<span class="carousel-arrow" style="left:14px"><svg width="10" height="12"><path d="M8 1L2 6l6 5z" fill="#888"/></svg></span>
<div class="listing" style="left:49px"><div role="img" aria-label="Photo of a Mediterranean style home with palm trees" style="background:linear-gradient(180deg,#7db3e6,#d8c27a 55%,#5c7a3a)"></div></div>
<div class="listing" style="left:227px"><div role="img" aria-label="Photo of a cream stucco home with red tile roof" style="background:linear-gradient(180deg,#5e9ad8,#e4c9a0 50%,#b86a3c)"></div></div>
<div class="listing" style="left:405px"><div role="img" aria-label="Photo of a modern blue multi-storey home" style="background:linear-gradient(180deg,#8fc0ea,#5d7f9e 50%,#3f5b74)"></div></div>
<div class="listing" style="left:583px"><div role="img" aria-label="Photo of a contemporary home with palm trees" style="background:linear-gradient(180deg,#5aa0e0,#c9b9a2 50%,#8a5a35)"></div></div>
<div class="listing" style="left:760px"><div role="img" aria-label="Photo of a stone two-storey house with lawn" style="background:linear-gradient(180deg,#9fc6e6,#a08c78 50%,#4e7a35)"></div></div>
<span class="carousel-arrow" style="left:928px"><svg width="10" height="12"><path d="M2 1l6 5-6 5z" fill="#888"/></svg></span>

<footer class="abs footer">
  <nav class="footer-nav"><span>Home</span><span>Our Story</span><span>Tenant</span><span>Owner</span><span>Contact us</span></nav>
  <div class="copyright">Copyright@2011</div>
  <div class="connect">Connect with us:<span class="dot"></span><span class="dot"></span><span class="dot"></span><span class="dot"></span></div>
</footer>
</body>
</html>
```